Women's Jewellery startup needs a captivating, beautifully designed and intuitive online store

[12/24 update]

Added 2 additional documents:

Feedback on designs received so far: designer feedback.docx
Product images from catalogue: products images.docx

Please read the feedback provided on designs provided so far to guide you further on your submission. The product images can be used to create promotional banners for the site.

@@@Added a document (VELISTO JEWELLERY_checklist.docx) which can be used by designers as a checklist when submitting their designs to ensure all aspects of the requirements have been covered @@@

+++IMPORTANT BUT NOT SPECIFIED IN THE REQUIREMENTS DOCUMENT - DESIGN SHOULD INCLUDE SUPPORT FOR MOBILE FRIENDLY SITE TOO+++

***Previous experience designing Jewellery online stores preferred (not essential)***

The name of the online Jewellery store is "Velisto Jewellery" and the business is based in Hong Kong. It will be run by 2 stay at home mothers. We need a Shopify themed store designed that will achieve the following objectives in order of priority:

• Conversion: The primary objective of the design/content is to prompt the customer to make a purchase. While this may sound obvious, it is mentioned so as not to distract the design process by focusing on other objectives (which are also important). The site also needs to be optimized so as to rank high in search engine searches for relevant keywords (SEO)
• Navigation: An intuitive interface which takes away a lot of the thinking from the customer by making it obvious what they need to do when they visit the store
• Engagement: Encourages the customer to spend time on the website and share content with their social network

Where applicable, the design of the store should reflect as closely as possible the mission statements and words outlined below:

• Jewellery you’ll fall in love with
• We want every client to leave the store with a smile
• We want to be able to provide the best service we can in every situation no matter what
• We aim to increase our business by word of mouth; therefore we tell people things about our store that makes it interesting for them to share
• We love every customer, no matter how difficult things get
• We, as a team, are so well informed about our products and brands that we always have the best information for our customers
• We celebrate women here!
• We celebrate life in here!
• We celebrate beauty here!
• We celebrate families here, as jewellery often stays within families.
• We will always try to make an extra step
• We will always try to exceed the expectation of our customers
• We will go as far as we possibly can to attract a customer back to our store and connect with us
• Every client that leaves our store knows more about jewellery because we passionately told him about it
• Romantic, classic, love, warm, cool, stylish

A draft functional specification is attached with this brief. We would like the design to reflect as closely as possible the functional requirements outlined in the document. Open to suggestions to improve upon the functional requirements.

Target Market(s)

Women aged 18-55

Industry/Entity Type

Jewelry Store

Coding

Coded - Design and coding required

Number of Pages Required

5+ page

Font styles to use
Other font styles liked:
• Myriad Pro as per Logo but open to any font that complements this one

Requirements
Must have
• 1. A look that encourages the user to make a purchase
• 2. An intuitive, easy to navigate and engaging interface
• 3. Primary colour scheme as defined in the functional specification attached
• 4. Simplistic look, not too cluttered
Nice to have
• 1. Closely matching the functional requirements of the site as outlined in the requirements specification but open to any better ideas

```html
<!DOCTYPE html>
<html lang="en">
<head>
<meta charset="utf-8">
<title>Velisto Jewellery – Newsletter</title>
<link href="https://fonts.googleapis.com/css2?family=Source+Sans+3:ital,wght@0,400;0,600;0,700;1,400&display=swap" rel="stylesheet">
<style>
:root{
  --gold:#d4a33a;
  --gold-dark:#b8862a;
  --ink:#222;
  --muted:#777;
  --line:#ddd;
  --paper:#fff;
  --night:#000;
  --slate:#3d4654;
  --scrim:rgba(0,0,0,.9);
}
*{box-sizing:border-box;margin:0;padding:0}
html,body{width:849px;height:1200px;overflow:hidden}
body{position:relative;background:var(--paper);font-family:"Source Sans 3",sans-serif;color:var(--ink)}
.abs{position:absolute}
.announce{left:0;top:0;width:849px;height:24px;background:linear-gradient(90deg,#6b5213,#a27c22,#6b5213);color:#fff;font-size:8px;text-align:center;line-height:24px}
.topbar{left:0;top:24px;width:849px;height:28px;background:var(--night);color:#ccc;font-size:7px;line-height:28px}
.topbar .currency{left:114px}
.topbar .account{right:115px;display:flex;gap:20px}
.brand{left:116px;top:72px;width:116px;text-align:center}
.brand-name{font-size:17px;font-weight:600;letter-spacing:3px;color:var(--gold-dark)}
.brand-tag{font-size:7px;font-style:italic;color:#555;margin-top:6px;white-space:nowrap}
.search{left:556px;top:70px;width:176px;height:23px;border:1px solid var(--line);border-radius:12px;font-size:8px;color:#999;padding:6px 10px}
.search svg{position:absolute;right:9px;top:6px}
.nav{top:114px;display:flex;gap:0;font-size:10px;color:#444}
.nav span{position:absolute;white-space:nowrap}
.nav .active{color:var(--gold)}
.hero{left:114px;top:164px;width:620px;height:298px;background:linear-gradient(100deg,#3a2c25,#1d1714 55%,#0d0b0a)}
.tile{top:462px;width:203px;height:102px;color:#fff;text-align:center;display:flex;flex-direction:column;justify-content:center}
.tile-diamond{left:114px;background:linear-gradient(135deg,#4b4b4b,#1a1a1a)}
.tile-gold{left:323px;background:linear-gradient(135deg,#c9952c,#7a5310)}
.tile-ruby{left:531px;background:linear-gradient(135deg,#5a1016,#1e0507)}
.tile small{font-size:9px;letter-spacing:1px}
.tile strong{font-size:14px;font-weight:400;letter-spacing:1px;margin:4px 0}
.tile-big strong{font-size:18px}
.filters{left:114px;top:576px;width:620px;height:78px;border:1px solid var(--line)}
.filter-label{top:592px;font-size:8px;color:#555}
.select{height:21px;border:1px solid var(--line);font-size:7px;color:#888;padding:5px 6px}
.select svg{position:absolute;right:5px;top:8px}
.range{left:588px;top:615px;width:128px;height:3px;background:var(--line)}
.range-knob{left:628px;top:610px;width:9px;height:9px;border-radius:50%;background:#aaa}
.range-num{top:627px;font-size:6px;color:#888}
.section-title{left:114px;top:688px;font-size:18px;font-weight:700;color:#333}
.card{top:738px;width:150px;height:236px;border:1px solid #eee;text-align:center}
.card-photo{position:absolute;left:0;top:0;width:150px;height:122px}
.card-name{position:absolute;top:134px;width:100%;font-size:11px;color:var(--gold)}
.card-desc{position:absolute;top:151px;left:20px;width:110px;font-size:7px;color:#888;line-height:11px}
.card-price{position:absolute;top:182px;width:100%;font-size:9px;font-weight:700}
.btn-add,.btn-view{position:absolute;top:205px;width:61px;height:19px;font-size:6px;line-height:19px}
.btn-add{left:12px;background:var(--gold);color:#fff}
.btn-view{left:77px;border:1px solid #999;color:#555}
.heart{position:absolute;left:8px;top:10px;width:16px;height:16px;border-radius:50%;background:#555}
.arrow{top:796px;width:28px;height:28px;border:1px solid var(--line)}
.arrow svg{position:absolute;left:9px;top:8px}
.footer{left:0;top:1005px;width:849px;height:195px;background:var(--night);color:#aaa}
.foot-head{top:1032px;font-size:10px;color:#fff}
.foot-list{top:1055px;font-size:7px;line-height:13px}
.social{font-size:7px;display:flex;align-items:center;gap:10px}
.social i{display:block;width:14px;height:14px;border-radius:50%;background:#444}
.foot-input{left:558px;top:1090px;width:176px;height:21px;border-radius:11px;background:#fff;font-size:7px;color:#888;padding:6px 10px;overflow:hidden}
.foot-input b{position:absolute;right:0;top:0;width:44px;height:21px;background:var(--gold);color:#fff;font-weight:400;text-align:center;line-height:21px}
.copyright{top:1170px;width:849px;text-align:center;font-size:7px}
.scrim{left:0;top:0;width:849px;height:1200px;background:var(--scrim)}
.modal{left:114px;top:234px;width:620px;height:228px;border:2.5px solid var(--gold);background:var(--night)}
.modal-photo{right:0;top:0;width:276px;height:223px;background:radial-gradient(ellipse at 60% 45%,#8a6550,#3a2418 55%,#0a0605 85%)}
.modal-title{left:30px;top:52px;font-size:24px;font-weight:700;color:#fff;white-space:nowrap}
.modal-title em{font-style:normal;color:var(--gold)}
.modal-text{left:30px;top:91px;width:300px;font-size:8.8px;line-height:14.5px;color:#fff}
.signup{left:30px;top:129px;width:295px;height:33px;border-radius:17px;background:#fff;overflow:hidden}
.signup span{position:absolute;left:10px;top:10px;font-size:9px;font-style:italic;color:#666}
.signup b{position:absolute;right:0;top:0;width:66px;height:33px;background:var(--gold);color:#fff;font-size:9px;font-weight:700;text-align:center;line-height:33px}
.close{left:712px;top:216px;width:40px;height:40px;border-radius:50%;background:var(--slate);color:#fff;font-size:21px;font-weight:700;text-align:center;line-height:40px}
</style>
</head>
<body>
<div class="page">
  <div class="abs announce">Free shipping on all orders over 500 HKD</div>
  <div class="abs topbar">
    <span class="abs currency">Currency: HKD ▾</span>
    <span class="abs account"><span>Sign in</span><span>Wishlist</span><span>Shopping Cart</span></span>
  </div>
  <div class="abs brand">
    <div class="brand-name">VELISTO</div>
    <div class="brand-tag">"Jewellery you'll fall in love with..."</div>
  </div>
  <div class="abs search">Search
    <svg width="9" height="9" viewBox="0 0 9 9"><circle cx="3.8" cy="3.8" r="2.8" fill="none" stroke="#888" stroke-width="1.2"/><line x1="6" y1="6" x2="8.5" y2="8.5" stroke="#888" stroke-width="1.2"/></svg>
  </div>
  <nav class="abs nav">
    <span class="active" style="left:452px">Home</span>
    <span style="left:510px">Shop</span>
    <span style="left:566px">Blog</span>
    <span style="left:621px">About Us</span>
    <span style="left:695px">Contact</span>
  </nav>
  <div class="abs hero" role="img" aria-label="Banner photo of a woman wearing earrings"></div>
  <div class="abs tile tile-diamond"><small>EXTRA</small><strong>10% OFF DIAMOND RINGS</strong><small>TILL MARCH 31ST, 2018</small></div>
  <div class="abs tile tile-gold tile-big"><strong>GOLD</strong><small>Shop the collection</small></div>
  <div class="abs tile tile-ruby tile-big"><strong>RUBY</strong><small>Shop the collection</small></div>
  <div class="abs filters"></div>
  <span class="abs filter-label" style="left:130px">Type</span>
  <span class="abs filter-label" style="left:239px">Collection</span>
  <span class="abs filter-label" style="left:364px">Metal</span>
  <span class="abs filter-label" style="left:475px">Gemstone</span>
  <span class="abs filter-label" style="left:586px">Price range</span>
  <div class="abs select" style="left:130px;top:608px;width:102px">Rings<svg width="6" height="4"><path d="M0 0l3 4 3-4z" fill="#999"/></svg></div>
  <div class="abs select" style="left:239px;top:608px;width:102px"></div>
  <div class="abs select" style="left:364px;top:608px;width:102px">Yellow gold<svg width="6" height="4"><path d="M0 0l3 4 3-4z" fill="#999"/></svg></div>
  <div class="abs select" style="left:475px;top:608px;width:102px">Diamond<svg width="6" height="4"><path d="M0 0l3 4 3-4z" fill="#999"/></svg></div>
  <div class="abs range"></div><div class="abs range-knob"></div>
  <span class="abs range-num" style="left:588px">Min</span>
  <span class="abs range-num" style="left:628px">500</span>
  <span class="abs range-num" style="left:706px">Max</span>
  <h2 class="abs section-title">TOP OF PRODUCTS</h2>
  <div class="abs select" style="left:469px;top:690px;width:99px;height:22px;font-size:8px">Our Favourites<svg width="6" height="4"><path d="M0 0l3 4 3-4z" fill="#999"/></svg></div>
  <div class="abs select" style="left:578px;top:690px;width:72px;height:22px">Newest first<svg width="6" height="4"><path d="M0 0l3 4 3-4z" fill="#999"/></svg></div>
  <div class="abs select" style="left:656px;top:690px;width:76px;height:22px">Price<svg width="6" height="4"><path d="M0 0l3 4 3-4z" fill="#999"/></svg></div>
  <div class="abs arrow" style="left:64px"><svg width="8" height="12"><path d="M7 1L2 6l5 5" fill="none" stroke="#999" stroke-width="1.5"/></svg></div>
  <div class="abs arrow" style="left:752px"><svg width="8" height="12"><path d="M1 1l5 5-5 5" fill="none" stroke="#999" stroke-width="1.5"/></svg></div>
  <article class="abs card" style="left:114px">
    <div class="card-photo" role="img" aria-label="Photo of two wedding rings" style="background:linear-gradient(135deg,#eee,#999)"></div><span class="heart"></span>
    <div class="card-name">Rings</div><p class="card-desc">Sed ut perspiciatis unde omnis iste natus error sit</p>
    <div class="card-price">$29.00 HKD</div><span class="btn-add">ADD TO CART</span><span class="btn-view">QUICK VIEW</span>
  </article>
  <article class="abs card" style="left:271px">
    <div class="card-photo" role="img" aria-label="Photo of a diamond bracelet" style="background:linear-gradient(135deg,#444,#0a0a0a)"></div><span class="heart"></span>
    <div class="card-name">Bracelets</div><p class="card-desc">Sed ut perspiciatis unde omnis iste natus error sit</p>
    <div class="card-price">$39.00 HKD</div><span class="btn-add">ADD TO CART</span><span class="btn-view">QUICK VIEW</span>
  </article>
  <article class="abs card" style="left:428px">
    <div class="card-photo" role="img" aria-label="Photo of a diamond necklace" style="background:linear-gradient(135deg,#333,#050505)"></div><span class="heart"></span>
    <div class="card-name">Necklaces</div><p class="card-desc">Sed ut perspiciatis unde omnis iste natus error sit</p>
    <div class="card-price">$28.00 HKD</div><span class="btn-add">ADD TO CART</span><span class="btn-view">QUICK VIEW</span>
  </article>
  <article class="abs card" style="left:585px">
    <div class="card-photo" role="img" aria-label="Photo of a woman wearing earrings" style="background:linear-gradient(135deg,#2a2a2a,#6a4a3e 60%,#1a1a1a)"></div><span class="heart"></span>
    <div class="card-name">Earrings</div><p class="card-desc">Sed ut perspiciatis unde omnis iste natus error sit</p>
    <div class="card-price">$27.00 HKD</div><span class="btn-add">ADD TO CART</span><span class="btn-view">QUICK VIEW</span>
  </article>
  <footer class="abs footer"></footer>
  <span class="abs foot-head" style="left:114px">About Us</span>
  <span class="abs foot-head" style="left:220px">Shopping</span>
  <span class="abs foot-head" style="left:321px">Customer Care</span>
  <span class="abs foot-head" style="left:443px">Social media</span>
  <span class="abs foot-head" style="left:558px">Signup to the Newsletter</span>
  <div class="abs foot-list" style="left:114px;color:var(--gold)">Our Story<br>Wholesale enquiries</div>
  <div class="abs foot-list" style="left:220px">Orders<br>Wishlist<br>Size Guide</div>
  <div class="abs foot-list" style="left:321px">Returns<br>FAQs<br>Care &amp; Warranty<br>Contact Us</div>
  <div class="abs social" style="left:448px;top:1059px"><i></i>Chatterbook</div>
  <div class="abs social" style="left:448px;top:1083px"><i></i>Snapgram</div>
  <div class="abs social" style="left:448px;top:1107px"><i></i>Pinboard</div>
  <div class="abs foot-list" style="left:558px;width:176px">Signup to stay in the loop. Receive updates, access to exclusive deals, and more.</div>
  <div class="abs foot-input">e-mail address<b>Sign Up</b></div>
  <div class="abs copyright">2017 Velisto Jewellery. All copyrights are reserved.</div>
</div>
<div class="abs scrim"></div>
<section class="abs modal">
  <div class="abs modal-photo" role="img" aria-label="Photo of a smiling woman wearing a necklace and earrings"></div>
  <h1 class="abs modal-title"><em>Newsletter</em> Subscription</h1>
  <p class="abs modal-text">Sed ut perspiciatis unde omnis iste natus error sit voluptatem accusantium doloremque laudantium, totam rem aperiam, eaque ipsa quae .</p>
  <div class="abs signup"><span>Email Address:</span><b>SIGN UP</b></div>
</section>
<div class="abs close">X</div>
</body>
</html>
```